Cat-products company needs smart, yet endearing, business card

We need a business card design for a new, but up-and-running, business based in Honolulu, Hawaii. The business is Purrnest Nook Co. Our first product is the most environmentally-friendly cat grass kit ever seen on the planet. Future products, currently in the R&D phase, will include a variety of exciting cat scratchers. We also do consulting work to help apartment-dwellers make their home more cat-friendly and, in the future, plan on doing full, custom installs of structure to create high walkways for cats.

Target Market(s)

Middle-aged, apartment-dwelling, middle-class workers who own 1 or more cats and who dote on them.

Industry/Entity Type

Pet Care

Contact Information for Business Card

A striking, professional, yet warm and friendly design is what we're after.

Font styles to use
Serif
Sans Serif
Other font styles liked:
• Comfortaa

Colors

Designer to choose colors to be used in the design.

Requirements
Must have
• The company logo: (see attachment)
• The company name: Purrnest Nook Co
• The web address: www.purrnestnookco.com
• Email: support@purrnestnookco.com
• Phone: +1 (808) 571 6023
• Update (Fri Jun 30 3017 7:45pm Hawaii Time) I would like, is possible, uploaded picture of the cat grass kit on the back of the card with some text along the lines of: Purrnest Nook Co - Maker Of The Leafiest Feline Sprout Set Yet
Nice to have
• A cat picture, cartoon, real or silhouette that illustrates cats in action and/or relaxing; ie using the apartment space to live, play and relax in and being well-contented.
• Most of the website is done in the font: Comfortaa. It might be nice to continue using this for brand consistency.
Should not have
• Hard-to-read fonts.

```html
<!DOCTYPE html>
<html lang="en">
<head>
<meta charset="utf-8">
<title>Purrnest Nook Co — Business Card</title>
<link rel="stylesheet" href="https://fonts.googleapis.com/css2?family=Roboto:wght@400;500;700&family=Roboto+Condensed:wght@500&display=swap">
<style>
  :root {
    --backdrop: #e2e2e2;
    --card: #f4f4f3;
    --brown: #4f2d24;
    --gold: #f0a500;
    --ink: #4a4a4a;
    --rule: #b9b9b9;
    --social: #8a6a5e;
  }
  * { margin: 0; padding: 0; box-sizing: border-box; }
  html, body {
    width: 1200px; height: 960px; overflow: hidden;
    background: var(--backdrop);
    font-family: "Roboto", Arial, sans-serif;
  }
  .card {
    position: absolute;
    width: 600px; height: 342px;
    background: var(--card);
    overflow: hidden;
  }
  .card--front { left: 314px; top: 113px; }
  .card--back { left: 311px; top: 472px; }

  /* Front */
  .brand {
    position: absolute; left: 0; top: 76px; width: 294px;
    display: flex; flex-direction: column; align-items: center;
  }
  .brand__dot {
    width: 62px; height: 62px; border-radius: 50%;
    background: var(--gold); margin-bottom: 18px;
  }
  .brand__name {
    font-weight: 700; font-size: 27px; color: var(--brown);
    letter-spacing: 0.2px; white-space: nowrap;
  }
  .divider {
    position: absolute; left: 294px; top: 77px;
    width: 1px; height: 192px; background: var(--rule);
  }
  .contact { position: absolute; left: 333px; top: 88px; }
  .contact__name {
    font-family: "Roboto Condensed", "Arial Narrow", sans-serif;
    font-weight: 500; font-size: 22px; color: var(--brown);
    line-height: 24px;
  }
  .contact__role {
    font-weight: 500; font-size: 15px; color: var(--gold);
    line-height: 20px; margin-top: 3px;
  }
  .contact__address {
    font-size: 14.5px; color: var(--ink); line-height: 18px; margin-top: 18px;
  }
  .contact__list { list-style: none; margin-top: 12px; }
  .contact__item {
    display: flex; align-items: center; gap: 8px;
    font-size: 14.5px; color: var(--ink); line-height: 19.5px;
  }
  .contact__icon { width: 14px; height: 14px; flex: none; fill: var(--brown); }
  .bands { position: absolute; left: 0; bottom: 0; }

  /* Back */
  .social {
    position: absolute; right: 16px; top: 19px;
    display: flex; gap: 2px;
  }
  .social__dot {
    width: 22px; height: 22px; border-radius: 50%; background: var(--social);
  }
  .pet-photo {
    position: absolute; left: 214px; top: 70px;
    width: 172px; height: 202px; border-radius: 50%;
    border: 1px solid #2a2a2a;
    background: radial-gradient(ellipse at 55% 40%, #1c1c1e 0%, #262426 38%, #7a4e34 62%, #c98a5a 100%);
  }
  .back__web {
    position: absolute; left: 0; top: 294px; width: 100%;
    text-align: center; font-size: 14.5px; color: var(--ink);
    letter-spacing: 5.2px;
  }
</style>
</head>
<body>
  <section class="card card--front">
    <div class="brand">
      <span class="brand__dot"></span>
      <span class="brand__name">Purrnest Nook Co</span>
    </div>
    <span class="divider"></span>
    <div class="contact">
      <p class="contact__name">MAREN KEALOHA</p>
      <p class="contact__role">CEO/FOUNDER</p>
      <p class="contact__address">2140 Lanai Vista Way<br>Honolulu, Hawaii 96815</p>
      <ul class="contact__list">
        <li class="contact__item">
          <svg class="contact__icon" viewBox="0 0 16 16"><path d="M3.5 1.5l2.3-.5 1.4 3.3-1.6 1.2c.8 1.8 2.1 3.1 3.9 3.9l1.2-1.6 3.3 1.4-.5 2.3c-.2.7-.8 1.1-1.5 1C6.3 12 3.9 9.7 2.5 3 2.4 2.3 2.8 1.7 3.5 1.5z"/></svg>
          +1 (808) 571 6023
        </li>
        <li class="contact__item">
          <svg class="contact__icon" viewBox="0 0 16 16"><path d="M1 3.5h14v1.2L8 9 1 4.7z"/><path d="M1 6.2l7 4.3 7-4.3v6.3H1z"/></svg>
          support@purrnestnookco.com
        </li>
        <li class="contact__item">
          <svg class="contact__icon" viewBox="0 0 16 16"><circle cx="8" cy="8" r="6.5"/><path d="M5 5.5c1 .2 1.8 1 1.6 2.2-.2.9 1 1.2.8 2.4L6.6 12 5 9.5 3.6 7.8z M9.5 3.2c1 .6 2.3.4 2.6 1.6.2 1-1 1.2-1.8 1.8-.6.5.2 1.5 1.2 1.6l1.3 1.2c-.3 1.3-1.2 2.3-2.4 2.8l.4-2c-.8-.3-1.5-1-1.4-2-1-.4-1.1-1.6-.3-2.2.5-.4.3-1.5.4-2.8z" fill="#f4f4f3"/></svg>
          www.purrnestnookco.com
        </li>
      </ul>
    </div>
    <svg class="bands" width="600" height="15" viewBox="0 0 600 15" aria-hidden="true">
      <polygon points="0,0 392,0 388,15 0,15" fill="var(--brown)"/>
      <polygon points="396,0 600,0 600,15 392,15" fill="var(--gold)"/>
    </svg>
  </section>

  <section class="card card--back">
    <div class="social" aria-hidden="true">
      <span class="social__dot"></span>
      <span class="social__dot"></span>
      <span class="social__dot"></span>
      <span class="social__dot"></span>
    </div>
    <div class="pet-photo" role="img" aria-label="Oval photo of a black cat asleep on a patterned orange cushion"></div>
    <p class="back__web">www.purrnestnookco.com</p>
  </section>
</body>
</html>
```